Thornbury Building Company - Card Design

I am looking to use the logo designs that you already did for me to develop a business card. I would like the card to have a black background and be double sided. I want white and green logo and text. I have attached an inspiration photo of a look that I like. I would like to use the Vertical Logo attached to take up the full front side of the card. On the back where I have my name and information, I would like to have the horizontal logo or maybe even just the image of the 'A' and trees without the text. I am open, but I am looking for something clean and simple and I want the green to really pop! Additional files can be found under Design #: 58302946

Target Market(s)

Homeowners

Industry/Entity Type

Construction

Contact Information for Business Card

Name: Marcus Thornbury, Title: Project Manager, Phone: 555.274.8136, Email: thornburybuildingcompany@mailvesta.com, address: 487 Larkspur Ln, Cedarvale, OR 95033, Lic# 2468317

Colors
00AB8E
00BBA5
67D7C9
C6EFE9
E9F9F6

Requirements
Nice to have
• I would like to see the logos that I have already got from ArtLoomHub, though I am open to new ones

```html
<!DOCTYPE html>
<html lang="en">
<head>
<meta charset="utf-8">
<title>Thornbury Building Company – Business Card</title>
<link href="https://fonts.googleapis.com/css2?family=Lato:wght@400;700;900&display=swap" rel="stylesheet">
<style>
  :root {
    --backdrop: #e7e4df;
    --card: #252323;
    --green: #5dbb46;
    --white: #ffffff;
    --muted: #d9d9d9;
  }
  * { margin: 0; padding: 0; box-sizing: border-box; }
  html, body { width: 1200px; height: 977px; overflow: hidden; }
  body {
    background: var(--backdrop);
    font-family: "Lato", Arial, sans-serif;
    position: relative;
  }
  .card {
    position: absolute;
    width: 640px;
    height: 366px;
    background: var(--card);
    border-radius: 22px;
    overflow: hidden;
    box-shadow: 0 10px 24px rgba(0,0,0,.25);
  }
  .card--front { left: 70px; top: 70px; }
  .card--back { left: 490px; top: 540px; }

  /* front */
  .front-lockup {
    position: absolute; left: 0; right: 0; top: 108px;
    display: flex; justify-content: center;
  }
  .brand-name {
    display: inline-flex; align-items: center; gap: 14px;
    color: var(--white); font-weight: 900; text-transform: uppercase;
  }
  .brand-mark { width: 22px; height: 22px; background: var(--green); flex: none; }
  .front-lockup .brand-name { font-size: 38px; letter-spacing: 1px; line-height: 1.1; text-align: center; }
  .front-lockup .brand-name .brand-mark { width: 30px; height: 30px; }
  .estd {
    position: absolute; top: 212px;
    color: var(--white); font-size: 14px; letter-spacing: 4px;
    padding: 6px 0; border-top: 1.5px solid var(--green); border-bottom: 1.5px solid var(--green);
  }
  .estd--label { left: 200px; }
  .estd--year { right: 200px; }

  /* back */
  .back-brand { position: absolute; right: 60px; top: 44px; }
  .back-brand .brand-name { font-size: 22px; }
  .rule { position: absolute; height: 1.5px; background: var(--green); }
  .rule--top { left: 250px; right: 40px; top: 112px; }
  .rule--mid { left: 40px; width: 300px; top: 214px; }
  .person { position: absolute; left: 40px; top: 150px; }
  .person__name { color: var(--green); font-weight: 900; font-size: 30px; text-transform: uppercase; line-height: 1; }
  .person__title { color: var(--white); font-size: 17px; margin-top: 6px; }
  .licence { position: absolute; right: 40px; top: 130px; color: var(--muted); font-size: 15px; }
  .contact { position: absolute; left: 40px; top: 228px; list-style: none; }
  .contact li { display: flex; align-items: center; gap: 10px; color: var(--white); font-size: 16px; line-height: 25px; }
  .contact svg { width: 13px; height: 13px; fill: var(--green); flex: none; }
  .band { position: absolute; bottom: 0; height: 16px; }
  .band--green { left: 0; width: 470px; background: var(--green); }
  .band--white { left: 478px; right: 0; background: var(--white); }
</style>
</head>
<body>

<section class="card card--front" aria-label="Card front">
  <div class="front-lockup">
    <span class="brand-name"><span class="brand-mark"></span><span>Thornbury<br>Building Company</span></span>
  </div>
  <span class="estd estd--label">ESTD</span>
  <span class="estd estd--year">2020</span>
</section>

<section class="card card--back" aria-label="Card back">
  <div class="back-brand">
    <span class="brand-name"><span class="brand-mark"></span>Thornbury Building Company</span>
  </div>
  <div class="rule rule--top"></div>
  <p class="licence">Lic# 2468317</p>
  <div class="person">
    <h1 class="person__name">Marcus Thornbury</h1>
    <p class="person__title">Project Manager</p>
  </div>
  <div class="rule rule--mid"></div>
  <ul class="contact">
    <li><svg viewBox="0 0 24 24"><path d="M6.6 10.8a15 15 0 0 0 6.6 6.6l2.2-2.2a1 1 0 0 1 1-.25 11.4 11.4 0 0 0 3.6.57 1 1 0 0 1 1 1V20a1 1 0 0 1-1 1A17 17 0 0 1 3 4a1 1 0 0 1 1-1h3.5a1 1 0 0 1 1 1c0 1.25.2 2.45.57 3.570a1 1 0 0 1-.25 1z"/></svg>555.274.8136</li>
    <li><svg viewBox="0 0 24 24"><path d="M2 5h20v14H2zM4 7v.5l8 5 8-5V7l-8 5z"/></svg>thornburybuildingcompany@mailvesta.com</li>
    <li><svg viewBox="0 0 24 24"><path d="M12 2a7 7 0 0 0-7 7c0 5 7 13 7 13s7-8 7-13a7 7 0 0 0-7-7zm0 9.5A2.5 2.5 0 1 1 12 6.5a2.5 2.5 0 0 1 0 5z"/></svg>487 Larkspur Ln, Cedarvale, OR 95033</li>
  </ul>
  <div class="band band--green"></div>
  <div class="band band--white"></div>
</section>

</body>
</html>
```